New business card/stationary for a consulting company

I am looking for a clean and very professional looking business card for my consulting company as well as corresponding stationary. I am uploading our logo. I like simple and powerful for the feel. No graphics but I am open on everything else. Below is my contact information but would like the final to be in a version I can add my employees information into and print. Thank you.

Daniel Whitcombe
dan@ferncliffadvisory.com
2870 North 9th Avenue, Summit Floor, Elm Ridge, Illinois 60531
www.ferncliffadvisory.com

Industry/Entity Type

Consulting

Contact Information for Business Card

Daniel Whitcombe
dan@ferncliffadvisory.com
www.ferncliffadvisory.com

Font styles to use
Serif
Sans Serif

Requirements
Must have
• Our logo and the business card details.
Nice to have
• our website www.ferncliffadvisory.com

```html
<!DOCTYPE html>
<html lang="en">
<head>
<meta charset="utf-8">
<title>Ferncliff Advisory — Business Card</title>
<link rel="stylesheet" href="https://fonts.googleapis.com/css2?family=Arimo:wght@400&family=Open+Sans:wght@400;700&display=swap">
<style>
  :root {
    --stage: #e4e5e7;
    --card: #ffffff;
    --navy: #1d1d6b;
    --ink-grey: #6a6a6a;
    --rule: #7a7a7a;
  }
  * { box-sizing: border-box; margin: 0; padding: 0; }
  html, body { width: 1200px; height: 904px; overflow: hidden; }
  body { background: var(--stage); position: relative; font-family: "Open Sans", sans-serif; }

  .card {
    position: absolute;
    width: 640px;
    height: 366px;
    background: var(--card);
    box-shadow: 0 6px 18px rgba(0,0,0,0.18);
  }
  .card--back { left: 90px; top: 64px; }
  .card--front { left: 470px; top: 474px; }

  /* back side */
  .back-mark {
    position: absolute; left: 50%; top: 50%;
    transform: translate(-50%, -50%);
    display: flex; align-items: center; gap: 12px;
  }
  .mark-square { width: 22px; height: 22px; background: var(--navy); }
  .brand-name {
    font-family: "Arimo", sans-serif; font-weight: 400;
    color: var(--navy); letter-spacing: 1px; white-space: nowrap;
  }
  .back-mark .brand-name { font-size: 20px; }

  /* front side */
  .front-brand {
    position: absolute; right: 48px; top: 48px;
    display: flex; flex-direction: column; align-items: flex-end; gap: 14px;
  }
  .front-brand .mark-square { width: 36px; height: 36px; margin-right: 150px; }
  .front-brand .brand-name { font-size: 22px; }

  .divider {
    position: absolute; left: 0; right: 28px; top: 196px;
    height: 1px; background: var(--rule);
  }

  .person { position: absolute; left: 40px; top: 226px; }
  .person-name { font-size: 19px; font-weight: 700; color: var(--navy); white-space: nowrap; }
  .person-rule { width: 220px; height: 1px; background: var(--rule); margin: 8px 0 8px -10px; }
  .address { font-size: 14px; line-height: 20px; color: var(--ink-grey); }

  .contacts { position: absolute; left: 318px; top: 218px; list-style: none; }
  .contacts li {
    display: flex; align-items: center; gap: 9px;
    font-size: 14px; line-height: 22px; color: var(--ink-grey);
  }
  .contacts svg { width: 15px; height: 15px; flex: none; }
</style>
</head>
<body>

<section class="card card--back" aria-label="Card back">
  <div class="back-mark">
    <span class="mark-square"></span>
    <span class="brand-name">FERNCLIFF ADVISORY</span>
  </div>
</section>

<section class="card card--front" aria-label="Card front">
  <div class="front-brand">
    <span class="mark-square"></span>
    <span class="brand-name">FERNCLIFF ADVISORY</span>
  </div>

  <div class="divider"></div>

  <div class="person">
    <p class="person-name">Daniel Whitcombe</p>
    <div class="person-rule"></div>
    <p class="address">2870 North 9th Avenue<br>Summit Floor, Elm Ridge<br>Illinois 60531</p>
  </div>

  <ul class="contacts">
    <li>
      <svg viewBox="0 0 16 16" aria-hidden="true">
        <circle cx="8" cy="8" r="8" fill="var(--navy)"/>
        <rect x="3.5" y="5" width="9" height="6" fill="none" stroke="#fff" stroke-width="1.1"/>
        <path d="M3.5 5 L8 8.5 L12.5 5" fill="none" stroke="#fff" stroke-width="1.1"/>
      </svg>
      dan@ferncliffadvisory.com
    </li>
    <li>
      <svg viewBox="0 0 16 16" aria-hidden="true">
        <circle cx="8" cy="8" r="8" fill="var(--navy)"/>
        <circle cx="8" cy="8" r="4.6" fill="none" stroke="#fff" stroke-width="1"/>
        <ellipse cx="8" cy="8" rx="2" ry="4.6" fill="none" stroke="#fff" stroke-width="1"/>
        <line x1="3.4" y1="8" x2="12.6" y2="8" stroke="#fff" stroke-width="1"/>
      </svg>
      www.ferncliffadvisory.com
    </li>
  </ul>
</section>

</body>
</html>
```